Black organic macadamia jar with creative, striking packaging design

Background of this project:

Started as a pioneer in the cultivation of organic macadamia nuts with small farmers, KORVENTA is now a leading global organic macadamia producer. The German-Kenyan company sees itself as a link between more than 5,000 small farmers in Africa and demanding quality customers around the world. A high level of technology enables direct support and promotion of small farmers and an effective refinement of macadamia nuts and other products on the organic mixed farms of the farmers. KORVENTA operates three modern, decentralized production facilities and a tree nursery in the immediate vicinity of the small farmers at the foot of Mount Selvaro. It has been pursuing a unique, holistic philosophy since it was founded.

The nuts are cracked and sorted by hand, which increases the quality enormously. The macadamias are sold for distribution to the food and cosmetics industries. Further information and the Korventa logo can be found at the following link: http://www.korventa-group.example/

if you want you can watch a video on Vidorama:
https://www.vidorama.example/watch?v=qTrWpLmXa9K&t=2s
short trailer: https://www.vidorama.example/watch?v=Xoet-HRPfsM

Next we want to offer our macadamia nuts to end consumers. The first stage are products for our online shop, the second stage is the food retail trade.

We chose the packaging variant of a sustainable round membrane can without aluminum membrane (probably) for 200 grams of macadamia nuts. The can should also be an attractive gift, can be placed directly on the table as a snack bowl and fits in a bottle holder (these are not design issues, however).

We are looking for a convincing, appealing design for the cans, which can then be printed on the cans.

Our thoughts on design:

- The design should represent the high quality of our macadamia nuts

- Our values should be communicated (organic, sustainable, healthy, personable)

- The design should be able to be used for several sizes of cans, if there will be larger and / or smaller cans in the future

- At the same time, it should not look as boring and simple as other organic products, but stand out clearly

- The design should be rather striking, extraordinary, as funky / funky as possible, but should still look professional.

- The can design must be black

- Of course, the Korventa logo should be included in the overall design (but that doesn't necessarily have to be dominant)

- The cans should have a recognition effect: "Ah, Korventa are the ones with these black cans" Our products should stand out as already written and should stand out from the competition if possible. (You can search for organic macadamia nuts on Shopvale, for example)

- Maybe African origin expressed by the design (not a must)

overall we do not want to limit your creativity for now, please let your ideas run wild!

If you have any questions, please do not hesitate to contact us, we will write comments and suggestions. We look forward to as many design suggestions as possible, thank you for that now, we are very excited! I wish you success!

our logo and product photos can be found here:
https: //www.filecrate. example / sh / 83k2rw4b1dzfm7q / BXT3n57JorQpEvyd9kLNHe2ub? dl = 0

Update 1:
We have a lot of high quality proposals, thank you guys. But I extended the deadline because still something special is missing. We want it really to be striking and extraordinary, it should "jump at you" when you see it.

Update 2:
Diameter of the can will probably be 7.3 cm, which means the scope is 22.9 cm and the heigh is around 10 - 11 cm

Update 3:
Guys we decided that we want a BLACK Can which looks noble and high quality, but is striking as well. Can be combined with Silver, Metalic etc. But Black is the main color and that will be the final requirement

Final update:
Thanks guys for all your efforts, your creative designs and drafts! Our team has chosen a winner!

Target Market(s)

Organic customers, online shoppers, later food retailers

Requirements
Must have
• - The design should represent the high quality of our macadamia nuts

- The design should be able to be used for several sizes of cans if there will be larger and / or smaller cans in the future

Nice to have
• see description
Should not have
• are open to everything at first, it shouldn't be boring

```html
<!DOCTYPE html>
<html lang="en">
<head>
<meta charset="utf-8">
<title>Korventa Organic Macadamia Nuts – Can Label</title>
<link href="https://fonts.googleapis.com/css2?family=Playfair+Display:wght@700&family=Montserrat:wght@400;600;700;800&family=Great+Vibes&display=swap" rel="stylesheet">
<style>
  :root {
    --stage: #d9d9d9;
    --can-black: #141210;
    --can-black-soft: #2a241e;
    --kraft: #c9a57a;
    --kraft-dark: #8f6a40;
    --ink: #1c1712;
    --paper: #ffffff;
  }
  * { box-sizing: border-box; margin: 0; padding: 0; }
  html, body { width: 709px; height: 1200px; overflow: hidden; }
  body {
    background: var(--stage);
    font-family: "Montserrat", Arial, sans-serif;
    color: var(--paper);
    position: relative;
  }

  /* ---------- wrap label ---------- */
  .wrap-label {
    position: absolute; left: 0; top: 300px;
    width: 709px; height: 340px;
    overflow: hidden;
  }
  .wrap-label__artwork {
    position: absolute; inset: 0;
    background: radial-gradient(circle at 50% 50%, var(--can-black-soft) 0%, var(--can-black) 70%);
  }

  .story-tab {
    position: absolute; left: 14px; top: 26px;
    width: 128px; height: 30px;
    background: var(--kraft); color: var(--ink);
    font-size: 11px; font-weight: 700; letter-spacing: 1px;
    display: flex; align-items: center; justify-content: center;
  }
  .story-box {
    position: absolute; left: 14px; top: 66px;
    width: 128px; height: 170px;
    border: 1px solid var(--kraft);
    color: var(--paper);
    padding: 10px 10px;
    font-size: 9.5px; line-height: 1.45;
    overflow: hidden;
  }

  .hand-badge {
    position: absolute; left: 152px; top: 34px;
    width: 76px; height: 76px;
  }

  .brand {
    position: absolute; left: 230px; top: 26px; width: 250px;
    display: flex; align-items: center; justify-content: center; gap: 8px;
  }
  .brand__dot { width: 22px; height: 22px; border-radius: 50%; background: var(--paper); }
  .brand__name { font-size: 20px; font-weight: 800; letter-spacing: 2px; color: var(--paper); }

  .product {
    position: absolute; left: 235px; top: 92px; width: 260px;
    text-align: center;
  }
  .product__organic { font-size: 12px; font-weight: 700; letter-spacing: 5px; color: var(--kraft); }
  .product__name {
    font-family: "Playfair Display", Georgia, serif;
    font-size: 40px; line-height: 1.05; color: var(--kraft); letter-spacing: 1px;
  }
  .product__rule { height: 2px; background: var(--kraft); margin: 6px 20px; }
  .product__tagline {
    font-family: "Great Vibes", cursive;
    font-size: 28px; color: var(--paper); margin-top: 4px;
  }

  .net-weight {
    position: absolute; right: 16px; top: 16px;
    font-size: 16px; font-weight: 800; color: var(--kraft);
  }
  .ingredients {
    position: absolute; left: 510px; top: 42px; width: 185px;
    font-size: 7px; line-height: 1.35; font-weight: 600; color: var(--paper);
  }
  .storage {
    position: absolute; left: 510px; top: 84px;
    font-size: 10px; font-weight: 800; color: var(--kraft); letter-spacing: .5px;
  }

  .nutrition {
    position: absolute; left: 510px; top: 104px;
    width: 185px; height: 222px;
    background: var(--paper); color: var(--ink);
    padding: 6px 8px;
    font-size: 7.5px;
  }
  .nutrition__title { font-size: 16px; font-weight: 800; border-bottom: 1px solid var(--ink); padding-bottom: 2px; }
  .nutrition__row { display: flex; justify-content: space-between; border-bottom: 1px solid #999; padding: 3px 0; }
  .nutrition__row--bold { font-weight: 700; }
  .nutrition__bar { height: 6px; background: var(--ink); margin: 3px 0; }

  /* ---------- lid label ---------- */
  .lid {
    position: absolute; left: 219px; top: 860px;
    width: 270px; height: 270px; border-radius: 50%;
    border: 6px solid var(--paper);
    background: radial-gradient(circle, var(--can-black-soft) 0%, var(--can-black) 75%);
    display: flex; flex-direction: column; align-items: center; justify-content: center;
    text-align: center;
  }
  .lid .brand { position: static; width: auto; margin-bottom: 16px; }
  .lid .brand__name { font-size: 17px; }
  .lid__name {
    font-family: "Playfair Display", Georgia, serif;
    font-size: 30px; line-height: 1.05; color: var(--kraft);
  }
  .lid__organic { font-size: 10px; font-weight: 700; letter-spacing: 4px; margin-top: 8px; color: var(--paper); }

  .stage-foliage {
    position: absolute; width: 200px; height: 260px; border-radius: 50%;
    background: radial-gradient(circle, rgba(150,150,150,.35), rgba(217,217,217,0) 70%);
  }
</style>
</head>
<body>

  <section class="wrap-label">
    <div class="wrap-label__artwork" role="img" aria-label="Hand-drawn macadamia branches, leaves and nuts engraved over the black can"></div>

    <div class="story-tab">OUR STORY</div>
    <div class="story-box">
      Grown by small farmers at the foot of the mountain, our organic macadamias are cracked and sorted by hand for the finest quality in every can.
    </div>

    <svg class="hand-badge" viewBox="0 0 76 76" aria-label="Sorted by hand stamp">
      <circle cx="38" cy="38" r="36" fill="none" stroke="#c9a57a" stroke-width="2"/>
      <circle cx="38" cy="38" r="27" fill="none" stroke="#c9a57a" stroke-width="1"/>
      <text x="38" y="35" text-anchor="middle" font-family="Montserrat, sans-serif" font-size="8" font-weight="800" fill="#ffffff">SORTED</text>
      <text x="38" y="46" text-anchor="middle" font-family="Montserrat, sans-serif" font-size="8" font-weight="800" fill="#ffffff">BY HAND</text>
    </svg>

    <div class="brand">
      <span class="brand__dot"></span>
      <span class="brand__name">KORVENTA</span>
    </div>

    <div class="product">
      <div class="product__organic">ORGANIC</div>
      <div class="product__rule"></div>
      <div class="product__name">MACADAMIA<br>NUTS</div>
      <div class="product__rule"></div>
      <div class="product__tagline">Straight From Nature</div>
    </div>

    <div class="net-weight">200G</div>
    <p class="ingredients">INGREDIENTS: 100% ORGANIC MACADAMIA NUTS, RAW, UNSALTED, HAND CRACKED AND SORTED.</p>
    <div class="storage">STORE IN DRY PLACE</div>

    <div class="nutrition">
      <div class="nutrition__title">Nutrition Facts</div>
      <div class="nutrition__row"><span>Serving Size</span><span>28g</span></div>
      <div class="nutrition__bar"></div>
      <div class="nutrition__row nutrition__row--bold"><span>Calories</span><span>200</span></div>
      <div class="nutrition__row nutrition__row--bold"><span>Total Fat</span><span>21g</span></div>
      <div class="nutrition__row"><span>Saturated Fat</span><span>3g</span></div>
      <div class="nutrition__row nutrition__row--bold"><span>Cholesterol</span><span>0mg</span></div>
      <div class="nutrition__row nutrition__row--bold"><span>Sodium</span><span>0mg</span></div>
      <div class="nutrition__row nutrition__row--bold"><span>Total Carbohydrate</span><span>4g</span></div>
      <div class="nutrition__row"><span>Dietary Fiber</span><span>2g</span></div>
      <div class="nutrition__row nutrition__row--bold"><span>Protein</span><span>2g</span></div>
    </div>
  </section>

  <div class="stage-foliage" style="left:-40px; top:820px;" role="img" aria-label="Faint sketched macadamia branch"></div>
  <div class="stage-foliage" style="right:-40px; top:860px;" role="img" aria-label="Faint sketched macadamia branch"></div>

  <section class="lid" role="group" aria-label="Lid label">
    <div class="brand">
      <span class="brand__dot"></span>
      <span class="brand__name">KORVENTA</span>
    </div>
    <div class="lid__name">MACADAMIA<br>NUTS</div>
    <div class="lid__organic">ORGANIC</div>
  </section>

</body>
</html>
```